International Clinical Software Company needs a new business card design

We are looking for a new business card design for our company that has recently expanded into the UK market, making us a multinational company.
After having rebranded our website and produced a new style guide, we are looking for a business card that is creative and attention grabbing, while being consistent with the style and colour scheme used on the new website, www.plumvora.example
We produce care management technology for the aged care market, but the main aspect we aim to communicate is the human element of our software, and the way it assists in providing better care for aged people, and stronger relationships between aged people and the staff that care for them.
Our current business card is a dark green with gold text, which makes the text quite difficult to read, not very aesthetically appealing and the colour scheme looks quite dated.
We would like something fresh and modern, that can still be colourful but doesn't use large blocks of dark colour, and uses the colours within our logo.
Something tying in with the leaves that are used in our logo could work quite nicely, along with the Autumn/Fall colours of soft greens, yellows and reds (also in our existing logo). However also happy to look at fresh, completely out of the box ideas we may not have yet considered.
Target Market(s)
The people that receive this business card work in the aged card or health industry and are either corporate/management level staff or clinical (Registered Nurses, care workers etc.)
Industry/Entity Type
Health Product
Contact Information for Business Card
Company Name - BrindlewayCare
Company locations: United Kingdom, Australia, New Zealand
Staff Details:
Staff name: Derek Mallow
Staff job title: Executive Chairman
Staff email: d.mallow@plumvora.example
Office phone number: 01742 918576
Font styles to use
Other font styles liked:
- Calibri
Requirements
Must have
- Must include the BrindlewayCare brand name in it's current font
- Must include logo (3 leaves in gold circle)
- Must include Business Card Details
Nice to have
- Elements of gold
- White space
- Something autumn themed but not too cliched
Should not have
- No blue - used by a major competitor and we would like to differentiate from them
- Large blocks of dark green colour (the green that appears in our leaves on the logo on our current business card is the background colour and it is far too dark)

```html
<!DOCTYPE html>
<html lang="en">
<head>
<meta charset="utf-8">
<title>BrindlewayCare – Business Card</title>
<link rel="stylesheet" href="https://fonts.googleapis.com/css2?family=Carlito:wght@400;700&display=swap">
<style>
  :root {
    --page-bg: #ece7dd;
    --card-bg: #ffffff;
    --gold-tan: #c2b595;
    --olive-gold: #b7b13a;
    --leaf-green: #5e8d3a;
    --rule-grey: #c9c9c4;
    --brand-tan: #b9ab88;
    --band-text: #ffffff;
  }
  * { box-sizing: border-box; margin: 0; padding: 0; }
  html, body {
    width: 1200px;
    height: 1022px;
    overflow: hidden;
    background: var(--page-bg);
    font-family: "Carlito", "Calibri", Arial, sans-serif;
  }
  .stage {
    width: 1200px;
    height: 1022px;
    display: flex;
    align-items: center;
    justify-content: center;
  }
  .card {
    position: relative;
    width: 1050px;
    height: 600px;
    background: var(--card-bg);
    border-radius: 14px;
    overflow: hidden;
    box-shadow: 0 10px 30px rgba(80, 60, 30, 0.18);
  }
  .brand {
    position: absolute;
    left: 70px;
    top: 120px;
    display: flex;
    align-items: center;
    gap: 26px;
  }
  .brand-mark {
    width: 110px;
    height: 110px;
    border-radius: 50%;
    background: var(--gold-tan);
  }
  .brand-name {
    font-size: 64px;
    font-weight: 400;
    color: var(--brand-tan);
    letter-spacing: 1px;
  }
  .holder {
    position: absolute;
    right: 70px;
    top: 70px;
    text-align: right;
  }
  .holder-name {
    font-size: 44px;
    font-weight: 700;
    color: var(--olive-gold);
    letter-spacing: 1px;
    line-height: 1;
  }
  .holder-title {
    font-size: 27px;
    color: var(--leaf-green);
    margin-top: 6px;
  }
  .divider {
    position: absolute;
    left: 300px;
    right: 250px;
    top: 300px;
    height: 1px;
    background: var(--rule-grey);
  }
  .contact {
    position: absolute;
    left: 300px;
    top: 335px;
    list-style: none;
    font-size: 25px;
    color: var(--olive-gold);
  }
  .contact li {
    display: flex;
    align-items: center;
    gap: 12px;
    margin-bottom: 6px;
  }
  .contact svg { width: 20px; height: 20px; }
  .band-green {
    position: absolute;
    left: 0;
    bottom: 0;
    width: 360px;
    height: 30px;
    background: var(--leaf-green);
  }
  .band-tan {
    position: absolute;
    right: 0;
    bottom: 0;
    width: 720px;
    height: 78px;
    background: var(--gold-tan);
    clip-path: polygon(40px 0, 100% 0, 100% 100%, 0 100%);
    display: flex;
    align-items: center;
    justify-content: flex-end;
    padding-right: 70px;
  }
  .locations {
    font-size: 27px;
    color: var(--band-text);
    letter-spacing: 0.5px;
  }
</style>
</head>
<body>
<main class="stage">
  <article class="card">
    <div class="brand">
      <div class="brand-mark"></div>
      <span class="brand-name">BrindlewayCare</span>
    </div>

    <div class="holder">
      <div class="holder-name">DEREK MALLOW</div>
      <div class="holder-title">Executive Chairman</div>
    </div>

    <div class="divider"></div>

    <ul class="contact">
      <li>
        <svg viewBox="0 0 20 20" aria-hidden="true"><path d="M5 2 C3 3 2 5 3 8 C5 13 8 16 12 17 C15 18 17 16 18 14 L14 11 L12 13 C10 12 8 10 7 8 L9 6 Z" fill="none" stroke="currentColor" stroke-width="1.8" stroke-linejoin="round"/></svg>
        01742 918576
      </li>
      <li>
        <svg viewBox="0 0 20 20" aria-hidden="true"><rect x="2" y="3" width="16" height="14" fill="none" stroke="currentColor" stroke-width="1.8"/><path d="M5 10 L9 14 L16 5" fill="none" stroke="currentColor" stroke-width="2"/></svg>
        d.mallow@plumvora.example
      </li>
    </ul>

    <div class="band-green"></div>
    <div class="band-tan"><span class="locations">United Kingdom, Australia, New Zealand</span></div>
  </article>
</main>
</body>
</html>
```